RTavenor Business Cards & Letterhead

I have a logo but need a design for some new business cards. We are a Design-Build Firm that specializes in the design and construction of commercial projects.
the cards need to be professional. no cartoon stuff.
i would like to have the cards in AI format so I can update the card as needed. Logo is provided.
Our Address is: 4187 Marlowe Ct. Apex, North Carolina 27614

```html
<!DOCTYPE html>
<html lang="en">
<head>
<meta charset="utf-8">
<title>RTavenor Business Card</title>
<link href="https://fonts.googleapis.com/css2?family=Open+Sans:wght@400;600;800&display=swap" rel="stylesheet">
<style>
  :root {
    --bg: #2b2f36;
    --card-white: #ffffff;
    --brand-blue: #1669b3;
    --deep-blue: #0b3a6c;
    --mid-blue: #14528f;
    --ink: #1e1e1e;
    --logo-gray: #3a3b3d;
    --soft-tint: #dfe5f1;
    --soft-tint-light: #eef1f8;
  }
  * { box-sizing: border-box; margin: 0; padding: 0; }
  html, body { width: 1200px; height: 780px; overflow: hidden; }
  body {
    background: var(--bg);
    font-family: "Open Sans", Arial, sans-serif;
    display: flex;
    align-items: center;
    justify-content: center;
    gap: 40px;
  }
  .card {
    position: relative;
    width: 540px;
    height: 309px;
    border-radius: 4px;
    overflow: hidden;
    box-shadow: 0 10px 30px rgba(0,0,0,0.35);
  }

  /* Front */
  .card-front { background: var(--card-white); }
  .front-tint {
    position: absolute;
    left: 250px; top: 150px;
    width: 230px; height: 159px;
    background: linear-gradient(160deg, var(--soft-tint) 0%, var(--soft-tint-light) 100%);
  }
  .wordmark {
    font-weight: 800;
    letter-spacing: 0.5px;
    display: flex;
    align-items: center;
    gap: 8px;
  }
  .wordmark-mark { width: 16px; height: 16px; }
  .wordmark sup { font-size: 9px; font-weight: 800; margin-left: 2px; }
  .front-logo {
    position: absolute;
    left: 30px; top: 28px;
    font-size: 30px;
    color: var(--logo-gray);
  }
  .front-logo .wordmark-mark { background: var(--brand-blue); }
  .contact {
    position: absolute;
    left: 34px; top: 112px;
    font-size: 12.5px;
    line-height: 1.45;
    color: var(--ink);
    list-style: none;
  }
  .contact-address { margin-bottom: 6px; }
  .contact-line { display: flex; align-items: center; gap: 7px; }
  .contact-line svg { width: 11px; height: 11px; flex: none; }
  .edge-rule {
    position: absolute;
    left: 14px; top: 190px;
    width: 3px; height: 119px;
    background: var(--brand-blue);
  }
  .holder {
    position: absolute;
    right: 60px; top: 196px;
    text-align: left;
  }
  .holder-name {
    font-size: 21px;
    font-weight: 600;
    color: var(--brand-blue);
    letter-spacing: 0.3px;
    text-transform: uppercase;
  }
  .holder-title {
    font-size: 14px;
    color: var(--ink);
    margin-top: 2px;
  }
  .accent-tab {
    position: absolute;
    right: 0; top: 200px;
    width: 34px; height: 44px;
    background: linear-gradient(90deg, var(--mid-blue), var(--brand-blue));
  }

  /* Back */
  .card-back {
    background: linear-gradient(115deg, var(--deep-blue) 0%, var(--mid-blue) 60%, var(--brand-blue) 100%);
  }
  .back-pattern {
    position: absolute; inset: 0;
    background: radial-gradient(ellipse at 85% 30%, rgba(40,130,210,0.35), rgba(11,58,108,0) 60%);
  }
  .back-logo {
    position: absolute;
    left: 50%; top: 50%;
    transform: translate(-50%, -50%);
    font-size: 34px;
    color: #ffffff;
  }
  .back-logo .wordmark-mark { background: #ffffff; }
</style>
</head>
<body>
  <section class="card card-front">
    <div class="front-tint" role="img" aria-label="Faint brand symbol decoration in soft blue-grey"></div>
    <div class="edge-rule"></div>
    <div class="front-logo wordmark"><span class="wordmark-mark"></span>RTAVENOR<sup>®</sup></div>
    <ul class="contact">
      <li class="contact-address">4187 Marlowe Ct. Apex,<br>North Carolina 27614</li>
      <li class="contact-line">
        <svg viewBox="0 0 12 12"><path d="M3 1l2 2.5-1.2 1.3a6 6 0 0 0 3.4 3.4L8.5 7 11 9l-1 2C5.5 11 1 6.5 1 2z" fill="#1669b3"/></svg>
        (919) 555-0148
      </li>
      <li class="contact-line">
        <svg viewBox="0 0 12 12"><circle cx="6" cy="6" r="5" fill="none" stroke="#1669b3" stroke-width="1.3"/><path d="M1 6h10M6 1c-2.5 3-2.5 7 0 10M6 1c2.5 3 2.5 7 0 10" fill="none" stroke="#1669b3" stroke-width="1"/></svg>
        www.rtavenor.com
      </li>
      <li class="contact-line">
        <svg viewBox="0 0 12 12"><rect x="1" y="2.5" width="10" height="7" rx="1" fill="none" stroke="#1669b3" stroke-width="1.3"/><path d="M1.5 3l4.5 3.5L10.5 3" fill="none" stroke="#1669b3" stroke-width="1.1"/></svg>
        MRT@RTavenor.com
      </li>
    </ul>
    <div class="holder">
      <p class="holder-name">Marcus Tavenor</p>
      <p class="holder-title">Founder/President</p>
    </div>
    <div class="accent-tab"></div>
  </section>

  <section class="card card-back">
    <div class="back-pattern" role="img" aria-label="Repeating brand symbol pattern in tonal blues"></div>
    <div class="back-logo wordmark"><span class="wordmark-mark"></span>RTAVENOR<sup>®</sup></div>
  </section>
</body>
</html>
```